Electric mountain bike tours nz

We are an Electric Mountain bike tour company in New Zealand. We will be offering bike rental and guided tours around the Nelson region in New Zealand. I want our website to represent both Mountain biking and New Zealand with the colours layout and features. We want tabs for the following:
-1 about us
-2 what we offer
-3 bookings/contact
Under the about us tab will be who we are as a a company. I want the ability to add videos to each of these tabs as we move foward with videos of the tracks we will be riding. I want the website to be editable so I can add and remove videos/photos myself. Also "our bikes" will be under this tab.
Under the what we offer tab will be
-1 bike rental and pricing
-2 guided tours and pricing
-3 recommended package deals.
I want to able to put the tracks under the guided tours tab and select beginner/ intermediate/advanced and have the tracks in each of the following to match the rider level. Also to be able to have a small video of the track would be great in this section.
Bookings and contact tab
(Further information for this tab to be updated soon)
Coded - Design and coding required
1 page
- Silver ferns, kiwi, mountains

```html
<!DOCTYPE html>
<html lang="en">
<head>
<meta charset="utf-8">
<title>Kowhai Rides – Electric Bike Tours NZ</title>
<link href="https://fonts.googleapis.com/css2?family=Lato:ital,wght@0,400;0,700;0,900;1,400;1,700;1,900&display=swap" rel="stylesheet">
<style>
:root{
  --green:#1f7a35;
  --green-dark:#17602a;
  --orange:#f27a22;
  --blue:#2c4fbf;
  --ink:#222;
  --grey:#666;
  --panel:#2b2b2b;
  --footer:#1b1b1b;
  --white:#fff;
}
*{box-sizing:border-box;margin:0;padding:0}
html,body{width:1200px;height:4534px;overflow:hidden}
body{font-family:'Lato',sans-serif;color:var(--ink);background:var(--white);position:relative}
.abs{position:absolute}
.btn{position:absolute;display:flex;align-items:center;justify-content:center;border-radius:22px;font-weight:700;font-size:14px;letter-spacing:.5px;text-transform:uppercase;text-decoration:none}
.btn-green{background:var(--green);color:var(--white)}
.btn-white{background:var(--white);color:var(--green)}
.btn-outline{border:2px solid var(--ink);color:var(--ink);background:var(--white)}
.h-italic{font-style:italic;font-weight:900;text-transform:uppercase}

/* header */
.site-header{top:0;left:0;width:1200px;height:116px;background:var(--white)}
.brand{left:100px;top:6px;width:190px;height:190px;border-radius:50%;background:var(--white);z-index:5;display:flex;align-items:center;justify-content:center;box-shadow:0 2px 8px rgba(0,0,0,.15)}
.brand span{font-weight:900;font-size:22px;color:var(--ink);text-align:center;line-height:1.1}
.main-nav{top:62px;left:555px;display:flex;gap:28px;font-size:15px;font-weight:700;text-transform:uppercase}
.main-nav a{color:var(--ink);text-decoration:none}
.main-nav a.active{border-bottom:2px solid var(--ink);padding-bottom:3px}

.hero{top:116px;left:0;width:1200px;height:590px;background:linear-gradient(160deg,#6f8a74 0%,#3f5a3c 45%,#5c6b3a 75%,#2f3a25 100%)}
.hero-title{top:318px;left:97px;color:var(--white);font-size:44px}
.hero-text{top:392px;left:97px;width:520px;color:var(--white);font-size:18px;line-height:1.4}

/* welcome */
.ghost{color:rgba(0,0,0,.06);font-weight:900;font-style:italic;text-transform:uppercase;white-space:nowrap}
.section-title{font-size:32px;text-align:center;width:1200px;left:0;color:var(--ink)}
.lead{left:290px;width:620px;text-align:center;font-size:13px;color:var(--grey);line-height:1.6}
.card{top:920px;width:310px;height:295px;background:var(--white);box-shadow:0 2px 10px rgba(0,0,0,.2);border:6px solid var(--white)}
.card .photo{width:100%;height:210px}
.card p{padding:14px 14px 0;font-weight:700;font-size:17px;color:#444;line-height:1.5}

/* split */
.split-left{top:1340px;left:0;width:600px;height:495px;background:linear-gradient(150deg,#1d2b22,#3a4a36 55%,#182218)}
.split-right{top:1340px;left:600px;width:600px;height:495px;background:linear-gradient(150deg,#2a8a3c,#1d6e2f)}
.split-title{color:var(--white);font-size:30px}
.split-text{color:var(--white);font-size:13px;line-height:1.6;width:400px}

/* packages */
.tabs{top:1925px;left:410px;display:flex;gap:14px;font-size:13px;font-weight:700;text-transform:uppercase}
.tabs span{padding:5px 10px}
.tabs .on{background:var(--panel);color:var(--white)}
.plan{background:var(--panel);color:var(--white)}
.plan-head{position:absolute;left:0;top:0;width:100%;display:flex;flex-direction:column;align-items:center;color:var(--white)}
.plan-name{font-size:26px;font-weight:900;font-style:italic;text-transform:uppercase;width:100%;text-align:center;padding:8px 0;border-bottom:1px solid rgba(255,255,255,.35)}
.price{margin-top:26px;font-weight:900;font-style:italic;font-size:70px;line-height:1}
.price sup{font-size:26px;vertical-align:top}
.price small{font-size:14px;font-weight:400;font-style:normal}
.plan-sub{position:absolute;width:100%;text-align:center;font-style:italic;font-size:20px;text-transform:uppercase}
.plan ul{position:absolute;width:100%;list-style:none;text-align:center;font-size:14px}
.plan li{height:51px;line-height:51px;border-bottom:1px solid rgba(255,255,255,.08)}

/* banner */
.banner{top:2825px;left:0;width:1200px;height:395px;background:linear-gradient(180deg,#7c93b0 0%,#53704f 50%,#233a22 80%,#46606b 100%)}
.banner-title{width:1200px;left:0;text-align:center;color:var(--white);font-size:38px;line-height:1.4}

/* about */
.about-title{top:3305px;left:100px;font-size:34px}
.about-text{left:100px;width:520px;font-size:13px;color:var(--grey);line-height:1.7}
.video-frame{left:735px;top:3315px;width:410px;height:280px;border:3px solid var(--green)}
.video-thumb{left:690px;top:3345px;width:410px;height:275px;background:linear-gradient(170deg,#9ab4c8,#6f8f5e 50%,#556b35)}

/* testimonials */
.quote{width:300px}
.avatar{position:absolute;left:0;top:0;width:64px;height:64px;border-radius:50%;background:#c9b9a8}
.stars{position:absolute;left:80px;top:0;color:#f2b01e;font-size:14px;letter-spacing:1px}
.quote p{position:absolute;left:80px;top:24px;width:220px;font-style:italic;font-size:12px;color:var(--grey);line-height:1.6}
.quote h4{position:absolute;left:0;top:110px;font-size:13px;font-weight:700}
.quote small{position:absolute;left:0;top:132px;font-size:12px;color:var(--grey);white-space:nowrap}

/* footer */
.site-footer{top:4160px;left:0;width:1200px;height:374px;background:var(--footer);color:var(--white)}
.footer-brand{left:130px;top:70px;width:125px;height:125px;border-radius:50%;background:var(--white);display:flex;align-items:center;justify-content:center;font-weight:900;font-size:15px;color:var(--ink);text-align:center;line-height:1.1}
.social{left:100px;top:228px;display:flex;gap:16px}
.social i{display:block;width:22px;height:22px;border-radius:50%;background:var(--white)}
.footer h5{font-size:16px;font-weight:700;text-transform:uppercase}
.links{list-style:none;font-size:13px;line-height:2.3}
.links li::before{content:"› ";font-weight:700}
.newsletter-input{left:830px;top:180px;width:270px;height:34px;background:var(--white);color:#999;font-size:12px;padding:10px}
.copyright{top:335px;left:0;width:1200px;text-align:center;font-size:13px}
</style>
</head>
<body>

<header class="abs site-header">
  <div class="abs brand"><span>KOWHAI<br>RIDES</span></div>
  <nav class="abs main-nav">
    <a class="active" href="#">Home</a><a href="#">About Us</a><a href="#">What We Offer</a><a href="#">Bookings</a><a href="#">Contact Us</a>
  </nav>
</header>

<section class="abs hero" role="img" aria-label="Mountain biker riding a grassy hillside trail with mountains behind"></section>
<div class="abs" style="top:392px;left:48px;color:#fff;font-size:22px">‹</div>
<div class="abs" style="top:392px;left:1140px;color:#fff;font-size:22px">›</div>
<h1 class="abs hero-title h-italic">Electric Bike Tours</h1>
<p class="abs hero-text">Nemo enim ipsam voluptatem quia voluptas sit aspernatur aut odit aut fugit, sed quia consequuntur magni.</p>
<a class="btn btn-green" style="top:488px;left:97px;width:172px;height:44px">Read More ➜</a>

<!-- welcome -->
<div class="abs ghost" style="top:752px;left:0;width:1200px;text-align:center;font-size:60px">Welcome to Kowhai Rides</div>
<h2 class="abs section-title h-italic" style="top:768px">Welcome to Kowhai Rides</h2>
<p class="abs lead" style="top:838px">At vero eos et accusamus et iusto odio dignissimos ducimus qui blanditiis praesentium voluptatum deleniti atque corrupti quos dolores et quas molestias excepturi sint occaecati cupiditate.</p>

<div class="abs card" style="left:100px"><div class="photo" role="img" aria-label="Cyclists beside an alpine lake with flowers" style="background:linear-gradient(170deg,#8fb5d8,#6a9a5a)"></div><p>The Summer Tours Feet Cycling City Name, NZ</p></div>
<div class="abs card" style="left:445px"><div class="photo" role="img" aria-label="Group of riders resting with their bikes" style="background:linear-gradient(170deg,#6f8f4a,#3e5a2e)"></div><p>The Summer Tours Feet Cycling City Name, NZ</p></div>
<div class="abs card" style="left:790px"><div class="photo" role="img" aria-label="Three riders on a countryside track" style="background:linear-gradient(170deg,#a6c2d4,#5b8a3c)"></div><p>The Summer Tours Feet Cycling City Name, NZ</p></div>

<a class="btn btn-green" style="top:1268px;left:405px;width:190px;height:44px">Book Your Bike</a>
<a class="btn btn-outline" style="top:1268px;left:610px;width:185px;height:44px">Download Guide</a>

<!-- split -->
<div class="abs split-left" role="img" aria-label="Rider standing with an electric mountain bike on a hillside"></div>
<div class="abs split-right"></div>
<svg class="abs" style="top:1330px;left:0" width="1200" height="515" viewBox="0 0 1200 515">
  <polygon points="0,10 600,70 1200,10 1200,0 0,0" fill="#fff"/>
  <polygon points="0,505 600,445 1200,505 1200,515 0,515" fill="#fff"/>
</svg>
<h3 class="abs split-title h-italic" style="top:1468px;left:97px">Bike Rental</h3>
<p class="abs split-text" style="top:1530px;left:97px">At vero eos et accusamus et iusto odio dignissimos ducimus qui blanditiis praesentium voluptatum deleniti atque corrupti quos dolores et quas molestias excepturi sint occaecati cupiditate non provident, similique sunt in culpa qui officia deserunt.</p>
<a class="btn btn-green" style="top:1658px;left:97px;width:150px;height:40px">Book Now ➜</a>
<h3 class="abs split-title h-italic" style="top:1468px;left:700px">Tours Guide</h3>
<p class="abs split-text" style="top:1530px;left:700px">At vero eos et accusamus et iusto odio dignissimos ducimus qui blanditiis praesentium voluptatum deleniti atque corrupti quos dolores et quas molestias excepturi sint occaecati cupiditate non provident, similique sunt in culpa qui officia deserunt.</p>
<a class="btn btn-white" style="top:1658px;left:700px;width:150px;height:40px">Download ➜</a>

<!-- packages -->
<div class="abs ghost" style="top:1838px;left:0;width:1200px;text-align:center;font-size:64px">Our Packages</div>
<h2 class="abs section-title h-italic" style="top:1862px">Our Packages</h2>
<div class="abs tabs"><span>Bike Rental</span><span>Guided Tours</span><span class="on">Recommended</span></div>

<div class="abs plan" style="top:2045px;left:100px;width:335px;height:610px">
  <div class="plan-head" style="height:170px;background:var(--orange)"><div class="plan-name">Starter</div><div class="price"><sup>$</sup>19<small> / MONTH</small></div></div>
  <div class="plan-sub" style="top:210px">Single Place Travel</div>
  <ul style="top:262px"><li>Lorem ipsum doloret</li><li>At vero eos et accusamus</li><li>Nam libero tempore coluta</li><li>Excepteur sint occaecat</li><li>On the other had esounce</li></ul>
  <a class="btn btn-green" style="top:535px;left:108px;width:120px;height:40px">Book Now</a>
</div>
<div class="abs plan" style="top:2008px;left:435px;width:333px;height:685px;z-index:2">
  <div class="plan-head" style="height:207px;background:var(--green)"><div class="plan-name">Standard</div><div class="price"><sup>$</sup>39<small> / MONTH</small></div></div>
  <div class="plan-sub" style="top:247px">Three Place Travel</div>
  <ul style="top:299px"><li>Nam libero tempore coluta</li><li>On the other had esounce</li><li>Lorem ipsum doloret</li><li>At vero eos et accusamus</li><li>Excepteur sint occaecat</li></ul>
  <a class="btn btn-green" style="top:598px;left:106px;width:120px;height:40px">Book Now</a>
</div>
<div class="abs plan" style="top:2045px;left:768px;width:332px;height:610px">
  <div class="plan-head" style="height:170px;background:var(--blue)"><div class="plan-name">Ultimate</div><div class="price"><sup>$</sup>59<small> / MONTH</small></div></div>
  <div class="plan-sub" style="top:210px">Five Place Travel</div>
  <ul style="top:262px"><li>Excepteur sint occaecat</li><li>Nam libero tempore coluta</li><li>At vero eos et accusamus</li><li>On the other had esounce</li><li>Lorem ipsum doloret</li></ul>
  <a class="btn btn-green" style="top:535px;left:106px;width:120px;height:40px">Book Now</a>
</div>

<!-- banner -->
<section class="abs banner" role="img" aria-label="Mountain lake with pine forest and snowy peak in New Zealand"></section>
<h2 class="abs banner-title h-italic" style="top:2925px">Book Your Electric Bike Tours<br>In New Zealand</h2>
<a class="btn btn-green" style="top:3062px;left:525px;width:150px;height:40px">Book Now ➜</a>

<!-- about -->
<div class="abs ghost" style="top:3480px;left:-120px;font-size:72px;transform:rotate(-90deg)">About Us</div>
<h2 class="abs about-title h-italic">Travel Further and Faster</h2>
<p class="abs about-text" style="top:3362px">Sed ut perspiciatis unde omnis iste natus error sit voluptatem accusantium doloremque laudantium, totam rem aperiam, eaque ipsa quae ab illo.</p>
<p class="abs about-text" style="top:3440px">Inventore veritatis et quasi architecto beatae vitae dicta sunt explicabo. Nemo enim ipsam voluptatem quia voluptas sit aspernatur aut odit aut fugit, sed quia consequuntur magni dolores eos qui ratione voluptatem sequi nesciunt. Neque porro quisquam est, qui dolorem ipsum quia dolor sit amet, consectetur, adipisci velit.</p>
<a class="btn btn-green" style="top:3582px;left:100px;width:158px;height:42px">Read More ➜</a>
<div class="abs video-frame"></div>
<div class="abs video-thumb" role="img" aria-label="Video of a rider on a mountain valley trail"></div>
<svg class="abs" style="top:3458px;left:871px" width="48" height="48" viewBox="0 0 48 48"><circle cx="24" cy="24" r="23" fill="#fff" fill-opacity=".9"/><polygon points="19,14 19,34 34,24" fill="#1f7a35"/></svg>

<div class="abs" style="top:3720px;left:100px;width:1000px;height:1px;background:#ddd"></div>

<!-- testimonials -->
<h2 class="abs section-title h-italic" style="top:3785px">Testimonials</h2>
<div class="abs" style="top:3970px;left:10px;font-size:24px;color:#777">‹</div>
<div class="abs" style="top:3970px;left:1165px;font-size:24px;color:#777">›</div>
<div class="abs quote" style="top:3868px;left:100px;height:150px">
  <div class="avatar" role="img" aria-label="Customer portrait"></div><div class="stars">★★★★☆</div>
  <p>“ At vero eos et accusamus et iusto odio dignissimos ducimus qui blanditiis praesentium voluptatum deleniti atque corrupti quos dolores et quas molestias ”</p>
  <h4>MARA LIND</h4><small>Creative Manager, NZ</small>
</div>
<div class="abs quote" style="top:3868px;left:445px;height:150px">
  <div class="avatar" role="img" aria-label="Customer portrait"></div><div class="stars">★★★★☆</div>
  <p>“ At vero eos et accusamus et iusto odio dignissimos ducimus qui blanditiis praesentium voluptatum deleniti atque corrupti quos dolores et quas molestias ”</p>
  <h4>TANE KERR</h4><small>Events Manager, NZ</small>
</div>
<div class="abs quote" style="top:3868px;left:795px;height:150px">
  <div class="avatar" role="img" aria-label="Customer portrait"></div><div class="stars">★★★★☆</div>
  <p>“ At vero eos et accusamus et iusto odio dignissimos ducimus qui blanditiis praesentium voluptatum deleniti atque corrupti quos dolores et quas molestias ”</p>
  <h4>IVO HARTLEY</h4><small>Sports Manager, NZ</small>
</div>
<svg class="abs" style="top:4070px;left:580px" width="40" height="10" viewBox="0 0 40 10"><circle cx="5" cy="5" r="4" fill="none" stroke="#555"/><circle cx="20" cy="5" r="4" fill="#1f7a35"/><circle cx="35" cy="5" r="4" fill="none" stroke="#555"/></svg>

<!-- footer -->
<footer class="abs site-footer footer">
  <div class="abs footer-brand">KOWHAI<br>RIDES</div>
  <div class="abs social"><i></i><i></i><i></i><i></i><i></i></div>
  <h5 class="abs" style="top:100px;left:415px">Quick Links</h5>
  <ul class="abs links" style="top:125px;left:415px"><li>Home</li><li>About Us</li><li>What We Offer</li><li>Tour Guide</li><li>Contact Us</li></ul>
  <ul class="abs links" style="top:125px;left:585px"><li>Info</li><li>Blog Post</li><li>Press</li><li>Privacy Policy</li><li>Terms of Service</li></ul>
  <h5 class="abs" style="top:100px;left:830px">Newsletter Subscription</h5>
  <p class="abs" style="top:128px;left:830px;width:270px;font-size:13px;line-height:1.5">Register your Email Address to get a more information about us</p>
  <div class="abs newsletter-input">Email</div>
  <a class="btn btn-green" style="top:228px;left:830px;width:100px;height:32px;font-size:12px">Subscribe</a>
  <div class="abs" style="top:295px;left:100px;width:1000px;height:1px;background:#444"></div>
  <p class="abs copyright">Copyrights © 2018 KOWHAI RIDES. All Rights Reserved.</p>
</footer>

</body>
</html>
```